Insert sheet for our Dog Food Package

We need an information sheet to go inn our pet food package, with branding, and information on ingredients, nutrition and feeding guidance. We will also need two additional items which will be a variation on the label design:
1) Label for package (detailed label about us and our food)
2) Label for outer shipping box (simple label for branding)
We will start with the information, insert page. The winning designer will then deliver the package and box labels as simplified versions of the same graphical theme.
I have attached samples of an earlier drafts of the insert piece. Please disregard the style, form and colors of the examples given. THEY ARE ONLY THERE TO SHOW WHAT INFORMATION SHOULD BE INCLUDED. All colors and style should be from our logo (attached). All graphics, font styles, and placement of elements need to be YOUR creative design - not a copy of the sample we gave. PLEASE READ THIS AND PLEASE DO NOT SUBMIT ANY VARIATION OF THE EXAMPLES!!!!!!!

Target Market(s)

Pet Owners

Industry/Entity Type

Pet Food

Colors
EB3D1F
EC4F4E
F09395
F8D3D4
FCEDEE

Requirements
Must have
• All new design. New colors (based in the palette of our logo), new graphics, new fonts, new placement of elements.
Should not have
• Please disregard the style, form and colors of the examples given. THEY ARE ONLY THERE TO SHOW WHAT INFORMATION SHOULD BE INCLUDED.

```html
<!DOCTYPE html>
<html lang="en">
<head>
<meta charset="utf-8">
<title>Marlo – Insert Sheet</title>
<link href="https://fonts.googleapis.com/css2?family=Ubuntu:wght@400;500;700&display=swap" rel="stylesheet">
<style>
  :root {
    --brown: #421812;
    --red: #b02127;
    --ink: #3a3a3d;
    --white: #ffffff;
    --paper-edge: #e2e3e5;
    --rule: #3a3a3d;
  }
  * { margin: 0; padding: 0; box-sizing: border-box; }
  html, body { width: 968px; height: 1200px; overflow: hidden; background: #ffffff; }
  body { font-family: 'Ubuntu', sans-serif; color: var(--ink); }
  .sheet {
    position: relative; width: 968px; height: 1200px; overflow: hidden;
    background: linear-gradient(90deg, var(--paper-edge) 0%, var(--white) 12%, var(--white) 88%, var(--paper-edge) 100%);
  }
  .backdrop { position: absolute; inset: 0; }
  .frame {
    position: absolute; left: 29px; top: 29px; width: 910px; height: 1143px;
    border: 8px solid var(--red);
  }
  .brand-mark {
    position: absolute; left: 185px; top: 76px; width: 242px; height: 242px;
    border-radius: 50%; background: var(--red); border: 9px solid var(--white);
    box-shadow: 0 0 0 3px var(--brown), 0 0 0 6px var(--white);
  }
  .brand-name {
    position: absolute; left: 440px; top: 150px;
    font-weight: 700; font-size: 96px; letter-spacing: 10px; line-height: 1;
    color: var(--red);
  }
  .story-title {
    position: absolute; left: 0; right: 0; top: 408px;
    display: flex; align-items: center; justify-content: center; gap: 18px;
    font-weight: 700; font-size: 48px; color: var(--ink);
  }
  .story-title::before, .story-title::after {
    content: ""; width: 210px; height: 3px; background: var(--brown);
  }
  .story-lead {
    position: absolute; left: 120px; right: 120px; top: 472px;
    text-align: center; font-weight: 500; font-size: 26px; line-height: 35px;
  }
  .story-body {
    position: absolute; left: 100px; right: 100px; top: 584px;
    text-align: center; font-size: 15.5px; line-height: 22px;
  }
  .love-band {
    position: absolute; left: 0; right: 0; top: 673px; height: 102px;
    background: var(--brown);
  }
  .love-title {
    position: absolute; left: 0; right: 0; top: 684px; text-align: center;
    font-weight: 700; font-size: 43px; color: var(--white); letter-spacing: 0.5px;
  }
  .panel {
    position: absolute; top: 746px; width: 411px; height: 396px;
    background: var(--white); border: 3px solid var(--rule);
  }
  .panel.nutrition { left: 63px; }
  .panel.feeding { left: 495px; }
  .panel-tab {
    height: 58px; background: var(--red); color: var(--white);
    font-weight: 700; font-size: 21px; display: flex; align-items: center; justify-content: center;
  }
  .panel-head {
    height: 51px; background: var(--brown); color: var(--white);
    font-size: 26px; display: flex; align-items: center; justify-content: center;
  }
  .facts { display: grid; grid-template-columns: 1fr 1fr; border-bottom: 3px solid var(--rule); }
  .fact {
    display: flex; justify-content: space-between; padding: 0 24px 0 28px;
    height: 30px; align-items: center; font-weight: 500; font-size: 18px;
  }
  .fact:nth-child(odd) { border-right: 3px solid var(--rule); }
  .fact:nth-child(-n+2) { border-bottom: 3px solid var(--rule); }
  .ingredients {
    padding: 14px 20px 0; text-align: center; font-size: 17.5px; line-height: 23px;
  }
  .feed-row {
    display: flex; justify-content: space-between; padding: 0 76px 0 24px;
    font-size: 18px; line-height: 27px; border-bottom: 3px solid var(--rule);
  }
  .feed-row:last-child { border-bottom: none; }
  .feed-row span:last-child { width: 60px; }
  .feed-row.labels { height: 44px; align-items: center; font-weight: 500; font-size: 22px; padding: 0 30px 0 20px; }
  .feed-row.labels span:last-child { width: auto; }
  .feed-group { display: flex; flex-direction: column; justify-content: center; }
  .feed-group .line { display: flex; justify-content: space-between; }
</style>
</head>
<body>
<main class="sheet">
  <svg class="backdrop" width="968" height="1200" viewBox="0 0 968 1200" aria-hidden="true">
    <rect x="0" y="0" width="968" height="430" fill="#421812"/>
    <path d="M0,395 C180,345 380,318 600,322 C760,326 880,330 968,332 L968,430 L0,430 Z" fill="#b02127"/>
    <path d="M0,412 C140,398 300,372 470,350 C620,332 780,338 968,330 L968,460 L0,460 Z" fill="#ffffff"/>
  </svg>
  <div class="frame"></div>

  <div class="brand-mark" role="img" aria-label="Brand emblem with dog illustration"></div>
  <div class="brand-name">MARLO</div>

  <h2 class="story-title">OUR STORY</h2>
  <p class="story-lead">We Revolutionzed the industry. Not Formulated to meed a minimum standard, but to develop the maximum health of the whole dog.</p>
  <p class="story-body">“we didn’t just set about to create a food that will ‘pass a minimum standard”. We set out to revolutionize the industry by creating a food that is designed with Superfoods, Wholesie Grains, and Powerful Oil to help your dog achieve their maximum health, happiness andlongevity.</p>

  <div class="love-band"></div>
  <h2 class="love-title">PREPARED WITH LOVE FOR SHADOW</h2>

  <section class="panel nutrition">
    <div class="panel-tab">We Prepared the best for shadow</div>
    <div class="panel-head">NUTRITIONAL INFORMATION</div>
    <div class="facts">
      <div class="fact"><span>Protein:</span><span>15%</span></div>
      <div class="fact"><span>Total Fat:</span><span>9.5%</span></div>
      <div class="fact"><span>Crude Fiber:</span><span>2.0%</span></div>
      <div class="fact"><span>Moisture:</span><span>72%</span></div>
    </div>
    <p class="ingredients">Potassium Citrate, DiCalcium Phosphate, Calcium Carbonate, Garbanzo Beans, Choline Bitartrate, Taurine, Salt, Zinc Proteinate, Magnesium Oxide, Iron Proteinate, Vitamin B-12, Selenium, Niacin, Riboflavin, Calcium Panthothenate, Thiamine, Vitamin A, Vitamin D, Calcium Lodate, Vitamin B6, Folic Acid</p>
  </section>

  <section class="panel feeding">
    <div class="panel-tab">How much should i feed shadow?</div>
    <div class="panel-head">RECOMMENDED FEEDING PLAN</div>
    <div class="feed-row labels"><span>Approximate weight</span><span>Full meal</span></div>
    <div class="feed-row" style="height:41px;align-items:center"><span>&lt;20 lbs</span><span>110 g</span></div>
    <div class="feed-row feed-group" style="height:93px">
      <div class="line"><span>20-29 lbs</span><span style="width:60px">200 g</span></div>
      <div class="line"><span>30-39 lbs</span><span style="width:60px">250 g</span></div>
      <div class="line"><span>40-54 lbs</span><span style="width:60px">300 g</span></div>
    </div>
    <div class="feed-row feed-group" style="height:63px">
      <div class="line"><span>50-69 lbs</span><span style="width:60px">350 g</span></div>
      <div class="line"><span>70-85 lbs</span><span style="width:60px">400 g</span></div>
    </div>
    <div class="feed-row" style="height:40px;align-items:center"><span>85+ lbs</span><span>500 g</span></div>
  </section>
</main>
</body>
</html>
```